Mindfulness School for Children -- Business Cards

We're looking for business cards for our school directors and owners. We're a mindfulness school for children called little lanterns. Attached are our logos/icons.

```html
<!DOCTYPE html>
<html lang="en">
<head>
<meta charset="utf-8">
<title>little lanterns – Business Card</title>
<link href="https://fonts.googleapis.com/css2?family=Arimo:wght@400;700&display=swap" rel="stylesheet">
<style>
  :root {
    --page-bg: #e9e9e9;
    --card-bg: #262626;
    --pattern-dark: #1c1c1c;
    --pattern-mid: #3a3a3a;
    --pattern-light: #8a8a8a;
    --text-light: #f2f2f2;
    --text-muted: #d6d6d6;
    --accent-teal: #5fc3d4;
    --accent-mint: #8fd3a8;
  }
  * { margin: 0; padding: 0; box-sizing: border-box; }
  html, body {
    width: 1200px; height: 900px; overflow: hidden;
    background: var(--page-bg);
    font-family: "Arimo", Arial, sans-serif;
  }
  .card {
    position: absolute; left: 250px;
    width: 700px; height: 400px;
    border-radius: 24px;
    overflow: hidden;
    box-shadow: 0 14px 30px rgba(0,0,0,0.22);
  }
  .card--front { top: 40px; background: var(--card-bg); color: var(--text-light); }
  .card--back { top: 460px; background: var(--card-bg); }

  .identity { position: absolute; left: 50px; top: 105px; }
  .identity__name { font-size: 27px; font-weight: 700; letter-spacing: 0.4px; color: var(--accent-teal); }
  .identity__role { font-size: 15.5px; color: var(--text-muted); margin-top: 3px; }
  .divider {
    position: absolute; left: 50px; top: 174px;
    width: 550px; height: 2px;
    background: linear-gradient(90deg, var(--accent-teal), var(--accent-mint) 55%, var(--accent-teal));
  }
  .contacts { position: absolute; left: 50px; top: 192px; list-style: none; }
  .contacts__item {
    display: flex; align-items: center; gap: 9px;
    font-size: 15.5px; line-height: 27px; color: var(--text-light);
  }
  .contacts__icon { width: 13px; height: 13px; fill: var(--accent-teal); flex: none; }
  .brand {
    position: absolute; right: 55px; top: 84px;
    display: flex; align-items: center; gap: 10px;
  }
  .brand__dot { width: 14px; height: 14px; border-radius: 50%; background: var(--accent-teal); }
  .brand__name { font-size: 40px; font-weight: 400; color: var(--accent-teal); letter-spacing: 0.4px; }
  .address {
    position: absolute; right: 90px; bottom: 48px;
    font-size: 15.5px; line-height: 22px; color: var(--text-light); font-style: normal;
  }

  .pattern-field {
    position: absolute; inset: 0;
    background: linear-gradient(125deg, var(--pattern-dark) 0%, var(--pattern-mid) 50%, var(--pattern-light) 100%);
  }
  .back-mark {
    position: absolute; right: 70px; bottom: 55px;
    display: flex; align-items: center; gap: 8px;
  }
  .back-mark__dot { width: 12px; height: 12px; border-radius: 50%; background: var(--accent-teal); }
  .back-mark__name { font-size: 22px; font-weight: 400; color: var(--accent-teal); }
</style>
</head>
<body>
  <section class="card card--front">
    <div class="brand">
      <span class="brand__dot"></span>
      <span class="brand__name">little lanterns</span>
    </div>

    <div class="identity">
      <p class="identity__name">MARA ELLISON</p>
      <p class="identity__role">CEO/Founder</p>
    </div>

    <div class="divider"></div>

    <ul class="contacts">
      <li class="contacts__item">
        <svg class="contacts__icon" viewBox="0 0 24 24"><path d="M6.6 10.8a15.1 15.1 0 0 0 6.6 6.6l2.2-2.2a1 1 0 0 1 1-.25 11.4 11.4 0 0 0 3.6.57 1 1 0 0 1 1 1V20a1 1 0 0 1-1 1A17 17 0 0 1 3 4a1 1 0 0 1 1-1h3.5a1 1 0 0 1 1 1c0 1.25.2 2.45.57 3.6a1 1 0 0 1-.25 1z"/></svg>
        (00) 3920 6614
      </li>
      <li class="contacts__item">
        <svg class="contacts__icon" viewBox="0 0 24 24"><path d="M7 1h10a2 2 0 0 1 2 2v18a2 2 0 0 1-2 2H7a2 2 0 0 1-2-2V3a2 2 0 0 1 2-2zm0 3v14h10V4zm5 15.5a1.2 1.2 0 1 0 0 2.4 1.2 1.2 0 0 0 0-2.4z"/></svg>
        (00) 2286 4031
      </li>
      <li class="contacts__item">
        <svg class="contacts__icon" viewBox="0 0 24 24"><path d="M2 5h20v14H2zm2 2v.5l8 5 8-5V7zm0 2.8V17h16V9.8l-8 5z"/></svg>
        hello@littlelanterns.com
      </li>
      <li class="contacts__item">
        <svg class="contacts__icon" viewBox="0 0 24 24"><path d="M12 2a10 10 0 1 0 0 20 10 10 0 0 0 0-20zm6.9 9h-3a15 15 0 0 0-1.3-6 8 8 0 0 1 4.3 6zM12 4.1c.9 1.2 1.8 3.4 2 6.9h-4c.2-3.5 1.1-5.7 2-6.9zM9.4 5a15 15 0 0 0-1.3 6h-3a8 8 0 0 1 4.3-6zM5.1 13h3a15 15 0 0 0 1.3 6 8 8 0 0 1-4.3-6zm6.9 6.9c-.9-1.2-1.8-3.4-2-6.9h4c-.2 3.5-1.1 5.7-2 6.9zm2.6-.9a15 15 0 0 0 1.3-6h3a8 8 0 0 1-4.3 6z"/></svg>
        www.littlelanterns.com
      </li>
    </ul>

    <address class="address">
      Po Box 4126 Willow Lane<br>
      Country Name, AB 30918
    </address>
  </section>

  <section class="card card--back">
    <div class="pattern-field" role="img" aria-label="Repeating flower pattern fading from black to silver across the card"></div>
    <div class="back-mark">
      <span class="back-mark__dot"></span>
      <span class="back-mark__name">little lanterns</span>
    </div>
  </section>
</body>
</html>
```